Exciting & Elegant Stationary Pack

Stationary consists of
1. Letter head / Envelope
2. Business Card
3. Invoice
4. 40x40mm sticker

Attached files;

1. Logo (Other formats available on request)
2. MS word Doc - For information and description of design
3. Website image (This will be our new website so use the colours so everything ties together)
4. Sample of stationary pack we like, but feel free to be creative

Target Market(s)

Home improvement

Industry/Entity Type

Construction

Font styles to use
Other font styles liked:
• Leave up to designer - We like font used on (website attached image)

Requirements
Must have
• Please look at uploaded file of sample website and use colours
Nice to have
• Any type of business card design - eg. metal, die cut, embossed, etc...

```html
<!DOCTYPE html>
<html lang="en">
<head>
<meta charset="utf-8">
<title>Stoneline Tiling – Business Card</title>
<link rel="stylesheet" href="https://fonts.googleapis.com/css2?family=PT+Sans:wght@400;700&display=swap">
<style>
  :root {
    --backdrop: #6a6a6a;
    --navy: #0f3d66;
    --orange: #f6882a;
    --white: #ffffff;
    --marble-light: #f4f4f2;
    --marble-mid: #dcdcdb;
    --marble-dark: #c9c9c8;
  }
  * { margin: 0; padding: 0; box-sizing: border-box; }
  html, body { width: 1200px; height: 750px; overflow: hidden; }
  body {
    background: var(--backdrop);
    font-family: "PT Sans", Tahoma, sans-serif;
    position: relative;
  }
  .card {
    position: absolute;
    width: 461px;
    height: 263px;
    overflow: hidden;
  }
  .card--front { left: 308px; top: 105px; }
  .card--back  { left: 475px; top: 412px; }

  .marble {
    position: absolute;
    inset: 0;
    background:
      linear-gradient(150deg, var(--marble-light) 0%, var(--marble-mid) 35%, var(--marble-light) 55%, var(--marble-dark) 80%, var(--marble-light) 100%);
  }

  .brand-name {
    position: absolute;
    color: var(--navy);
    font-weight: 700;
    line-height: 1;
    text-align: right;
  }
  .brand-name__main { display: block; font-size: 32px; letter-spacing: 1px; }
  .brand-name__sub  { display: block; font-size: 16px; letter-spacing: 2px; margin-top: 6px; }
  .card--front .brand-name { left: 140px; top: 44px; }
  .card--back  .brand-name { left: 272px; top: 156px; }

  .contact-band {
    position: absolute;
    left: 0; right: 0; bottom: 0;
    height: 84px;
    background: var(--navy);
    border-top: 3px solid var(--orange);
    color: var(--white);
  }
  .holder { position: absolute; left: 22px; top: 7px; }
  .holder__name { color: var(--orange); font-weight: 700; font-size: 19px; line-height: 22px; }
  .holder__role, .holder__licence { font-size: 14px; line-height: 19px; }

  .contacts {
    position: absolute;
    left: 271px; top: 13px;
    list-style: none;
  }
  .contacts li {
    display: flex;
    align-items: center;
    gap: 7px;
    font-size: 14px;
    line-height: 17.5px;
    white-space: nowrap;
  }
  .contacts svg { width: 11px; height: 11px; flex: none; }
</style>
</head>
<body>

  <section class="card card--front" aria-label="Business card front">
    <div class="marble" role="img" aria-label="White marble stone texture"></div>
    <div class="brand-name">
      <span class="brand-name__main">STONELINE</span>
      <span class="brand-name__sub">TILING</span>
    </div>
    <div class="contact-band">
      <div class="holder">
        <p class="holder__name">Linh Tran</p>
        <p class="holder__role">Project Manager</p>
        <p class="holder__licence">Lic No.,204519c</p>
      </div>
      <ul class="contacts">
        <li>
          <svg viewBox="0 0 11 11" aria-hidden="true"><rect x="2.5" y="0.5" width="6" height="10" rx="1" fill="none" stroke="var(--orange)" stroke-width="1.4"/><rect x="4.3" y="8" width="2.4" height="1" fill="var(--orange)"/></svg>
          <span>0400 318 752</span>
        </li>
        <li>
          <svg viewBox="0 0 11 11" aria-hidden="true"><rect x="0.5" y="2" width="10" height="7" fill="var(--orange)"/><path d="M0.5 2 L5.5 6 L10.5 2" fill="none" stroke="var(--navy)" stroke-width="1"/></svg>
          <span>info@stoneline.com.au</span>
        </li>
        <li>
          <svg viewBox="0 0 11 11" aria-hidden="true"><circle cx="5.5" cy="5.5" r="5" fill="var(--orange)"/><ellipse cx="5.5" cy="5.5" rx="2" ry="5" fill="none" stroke="var(--navy)" stroke-width="0.8"/><line x1="0.5" y1="5.5" x2="10.5" y2="5.5" stroke="var(--navy)" stroke-width="0.8"/></svg>
          <span>www.stoneline.com.au</span>
        </li>
      </ul>
    </div>
  </section>

  <section class="card card--back" aria-label="Business card back">
    <div class="marble" role="img" aria-label="White marble stone texture"></div>
    <div class="brand-name">
      <span class="brand-name__main">STONELINE</span>
      <span class="brand-name__sub">TILING</span>
    </div>
  </section>

</body>
</html>
```